HR services to some of biggest Silicon Valley Tech companies needs a new website

We need a new website design probably 4-5 pages initially. Here are some websites we like the look of https://quenmarport.com/ , https://www.vribly.com/ and https://fennix.com/ .

Target Market(s)

Silicon valley tech companies

Industry/Entity Type

HR

Coding

Coded - Design and coding required

Number of Pages Required

5+ page

Requirements
Nice to have
• any stock photos or images should show a diverse group of people. Our client base is very diverse

```html
<!DOCTYPE html>
<html lang="en">
<head>
<meta charset="utf-8">
<title>Brightpath HR Consulting</title>
<link href="https://fonts.googleapis.com/css2?family=Montserrat:wght@400;500;600;700&family=Roboto:wght@400;500&display=swap" rel="stylesheet">
<style>
:root{
  --yellow:#f5c10e;
  --yellow-deep:#e9b400;
  --ink:#222222;
  --text:#444444;
  --muted:#777777;
  --band:#5a5a5c;
  --card:#ececec;
  --footer:#1b1b1b;
  --white:#ffffff;
}
*{box-sizing:border-box;margin:0;padding:0}
html,body{width:1200px;height:4373px;overflow:hidden}
body{position:relative;background:var(--white);font-family:"Montserrat",sans-serif;color:var(--text)}
.abs{position:absolute}

/* header */
.topbar{left:463px;top:0;width:737px;height:60px;background:var(--yellow);display:flex;align-items:center;padding-left:110px;gap:10px}
.social-dot{width:32px;height:32px;border-radius:50%;background:var(--white)}
.callout{margin-left:30px;font-size:13px;font-weight:600;color:var(--ink);display:flex;align-items:center;gap:10px}
.callout strong{font-size:20px;font-weight:700}
.brand{left:110px;top:62px;width:150px}
.brand .mark{width:22px;height:22px;border-radius:50%;background:var(--yellow);margin:0 auto 6px}
.brand .name{font-size:21px;font-weight:600;color:var(--ink);letter-spacing:1px;text-align:center;line-height:1}
.brand .sub{font-size:11px;letter-spacing:4px;color:var(--ink);text-align:center;margin-top:3px}
.nav{left:362px;top:96px;display:flex;gap:43px;font-size:13px;font-weight:600;color:var(--ink)}
.nav .active{color:var(--yellow)}

/* hero */
.hero{left:0;top:141px;width:1200px;height:600px;background:linear-gradient(135deg,#6f6259 0%,#9c8c7d 45%,#5d5148 100%)}
.hero-title{left:0;top:358px;width:1200px;text-align:center;font-size:50px;font-weight:700;color:var(--white)}
.hero-sub{left:0;top:428px;width:1200px;text-align:center;font-size:22px;font-weight:700;color:var(--yellow)}
.arrow-btn{font-size:14px;font-weight:700;color:var(--ink);display:flex;align-items:center;justify-content:center}
.scroll-down{left:565px;top:706px;width:70px;height:70px;border-radius:50%;background:var(--white);box-shadow:0 4px 12px rgba(0,0,0,.25)}

/* about */
.about-mark{left:130px;top:875px;width:450px;height:395px}
h2.section{font-size:40px;font-weight:700;color:var(--ink)}
.about-title{left:617px;top:915px}
.about-list{left:617px;top:970px;width:480px;list-style:none}
.about-list li{display:flex;gap:14px;font-size:13px;line-height:22px;margin-bottom:22px;color:var(--muted)}
.about-list svg{flex:none;margin-top:5px}

/* services */
.services-title{left:0;top:1355px;width:1200px;text-align:center}
.services-band{left:0;top:1456px;width:1200px;height:362px;background:var(--band)}
.service{top:1456px;width:300px;height:362px;padding:30px 32px 0}
.service.featured{top:1431px;height:404px;padding-top:55px;background:linear-gradient(160deg,#6a5f4f,#3f4450 60%,#2d3340)}
.service h3{margin-top:18px;font-size:21px;font-weight:700;color:var(--yellow);line-height:26px}
.service p{margin-top:14px;font-size:13.5px;line-height:21.5px;color:var(--white)}
.service .go{position:absolute;left:32px;bottom:26px}
.service.featured .go{bottom:46px}

/* how it works */
.how-title{left:0;top:1927px;width:1200px;text-align:center}
.step{width:313px;height:358px;background:var(--card);border-radius:6px;padding:32px 37px}
.step.hot{background:linear-gradient(90deg,#545254 0%,#8a7a45 45%,var(--yellow) 100%)}
.step .label{margin-top:20px;font-size:15px;font-weight:600;color:var(--ink)}
.step h3{margin-top:12px;font-family:"Roboto",sans-serif;font-size:26px;font-weight:500;color:var(--ink)}
.step p{margin-top:14px;font-size:12.5px;line-height:21.5px;color:var(--muted)}
.step.hot .label,.step.hot h3,.step.hot p{color:var(--white)}

/* team */
.team{left:0;top:2840px;width:1200px;height:478px;background:linear-gradient(110deg,#c9ccd0 0%,#8c8f93 35%,#e2e0dc 55%,#6f6a62 100%)}
.team-rule{left:0;top:2840px;width:1200px;height:8px;background:linear-gradient(90deg,#555 0%,var(--yellow) 100%)}
.team-rule.bottom{top:3310px}
.team-title{left:0;top:2896px;width:1200px;text-align:center}
.team-sub{left:340px;top:2954px;width:520px;text-align:center;font-size:22px;font-weight:600;color:var(--ink);line-height:28px}
.play{left:567px;top:3134px;width:66px;height:66px;border-radius:50%;background:var(--yellow);border:4px solid #d29f00}

/* testimonial */
.say-title{left:0;top:3405px;width:1200px;text-align:center}
.quote{left:563px;top:3466px;width:74px;height:74px;border-radius:50%;border:3px solid #cfcfcf;background:var(--white)}
.say-text{left:205px;top:3560px;width:790px;text-align:center;font-size:13.5px;line-height:21.5px;font-style:italic;color:var(--muted);font-family:"Roboto",sans-serif}
.say-name{left:0;top:3662px;width:1200px;text-align:center;font-size:16px;font-weight:500;color:var(--text)}
.dots{left:565px;top:3736px;display:flex;gap:5px}
.dots span{width:11px;height:11px;border-radius:50%;border:1.5px solid #777}
.dots span.on{background:#777}

/* clients */
.client{top:3851px;width:186px;height:90px;border:1px solid #ddd;display:flex;align-items:center;justify-content:center;gap:8px;font-size:20px;font-weight:600;color:#555}
.client i{width:14px;height:14px;border-radius:50%;background:var(--yellow);display:block}

/* footer */
.footer{left:0;top:4046px;width:1200px;height:327px;background:var(--footer)}
.fcol{top:4112px;color:var(--white)}
.fcol h4{font-size:17px;font-weight:700;margin-bottom:22px}
.fcol li{list-style:none;font-size:14px;line-height:21.5px}
.fcol .ic{display:flex;gap:10px}
.fcol .ic svg{flex:none;margin-top:4px}
.frule{left:111px;top:4312px;width:978px;height:1px;background:#777}
.copy{left:0;top:4334px;width:1200px;text-align:center;font-size:12px;color:var(--white)}
</style>
</head>
<body>

<header>
  <div class="abs topbar">
    <span class="social-dot"></span><span class="social-dot"></span><span class="social-dot"></span><span class="social-dot"></span>
    <span class="callout">
      <svg width="18" height="18" viewBox="0 0 24 24"><path d="M6.6 10.8a15 15 0 0 0 6.6 6.6l2.2-2.2a1 1 0 0 1 1-.25 11.4 11.4 0 0 0 3.6.6 1 1 0 0 1 1 1V20a1 1 0 0 1-1 1A17 17 0 0 1 3 4a1 1 0 0 1 1-1h3.5a1 1 0 0 1 1 1c0 1.25.2 2.45.6 3.6a1 1 0 0 1-.25 1z" fill="#222"/></svg>
      CALL US TODAY : <strong>+1 888 888 8888</strong>
    </span>
  </div>
  <div class="abs brand">
    <div class="mark"></div>
    <div class="name">BRIGHTPATH</div>
    <div class="sub">HR CONSULTING</div>
  </div>
  <nav class="abs nav">
    <span class="active">HOME</span><span>WHAT WE DO</span><span>HOW IT WORKS</span><span>OUR CLIENTS</span><span>ABOUT US</span><span>CONTACT US</span>
  </nav>
</header>

<section>
  <div class="abs hero" role="img" aria-label="Photo of a diverse team of smiling professionals around a meeting table"></div>
  <h1 class="abs hero-title">BRIGHTPATH HR CONSULTING</h1>
  <p class="abs hero-sub">OUR TEAM SUPPORTS YOURS</p>
  <svg class="abs" style="left:503px;top:470px" width="194" height="46" viewBox="0 0 194 46"><polygon points="18,0 176,0 194,23 176,46 18,46 0,23" fill="#f5c10e"/><text x="97" y="28" text-anchor="middle" font-family="Montserrat,sans-serif" font-size="14" font-weight="700" fill="#222">LEARN MORE</text></svg>
  <div class="abs scroll-down">
    <svg width="70" height="70" viewBox="0 0 70 70"><path d="M35 20v30M25 40l10 10 10-10" stroke="#222" stroke-width="3" fill="none"/></svg>
  </div>
</section>

<section>
  <svg class="abs about-mark" viewBox="0 0 450 395" role="img" aria-label="Brightpath brand emblem">
    <defs><linearGradient id="em" x1="0" y1="0" x2="1" y2="1"><stop offset="0" stop-color="#b88a22"/><stop offset="1" stop-color="#4a4642"/></linearGradient></defs>
    <circle cx="225" cy="197" r="175" fill="url(#em)"/>
    <text x="225" y="210" text-anchor="middle" font-family="Montserrat,sans-serif" font-size="40" font-weight="700" fill="#ffffff">BRIGHTPATH</text>
  </svg>
  <h2 class="abs section about-title">ABOUT US</h2>
  <ul class="abs about-list">
    <li><svg width="12" height="12" viewBox="0 0 12 12"><circle cx="6" cy="6" r="5.5" fill="#f5c10e"/><path d="M3.3 6.2l1.8 1.7 3.6-3.6" stroke="#fff" stroke-width="1.4" fill="none"/></svg><span>Brightpath HR Consulting is the solution to all your HR issues. We are a one-stop-shop providing a variety of services</span></li>
    <li><svg width="12" height="12" viewBox="0 0 12 12"><circle cx="6" cy="6" r="5.5" fill="#f5c10e"/><path d="M3.3 6.2l1.8 1.7 3.6-3.6" stroke="#fff" stroke-width="1.4" fill="none"/></svg><span>Whether you have a specific HR need or seek relief by outsourcing altogether, we have you covered</span></li>
    <li><svg width="12" height="12" viewBox="0 0 12 12"><circle cx="6" cy="6" r="5.5" fill="#f5c10e"/><path d="M3.3 6.2l1.8 1.7 3.6-3.6" stroke="#fff" stroke-width="1.4" fill="none"/></svg><span>For some clients, a Brightpath Consultant is known as the HR department and for others, we simply step in as needed on a project basis</span></li>
  </ul>
  <svg class="abs" style="left:617px;top:1177px" width="204" height="40" viewBox="0 0 204 40"><polygon points="16,2 188,2 202,20 188,38 16,38 2,20" fill="#f5c10e" stroke="#6a6a6a" stroke-width="2"/><polygon points="20,4 184,4 198,20 184,36 20,36 6,20" fill="#f5c10e"/><text x="102" y="25" text-anchor="middle" font-family="Montserrat,sans-serif" font-size="13.5" font-weight="700" fill="#222">LEARN MORE</text></svg>
</section>

<section>
  <h2 class="abs section services-title">OUR SERVICES</h2>
  <div class="abs services-band"></div>

  <article class="abs service" style="left:0">
    <svg width="60" height="60" viewBox="0 0 60 60" fill="none" stroke="#f5c10e" stroke-width="2"><circle cx="16" cy="16" r="10"/><circle cx="42" cy="16" r="10"/><circle cx="16" cy="42" r="10"/><circle cx="42" cy="42" r="10"/><path d="M11 16l4 4 7-8"/></svg>
    <h3>Setup</h3>
    <p>Select and implement an HRIS system<br>Create Company Handbook<br>Write termination procedure<br>Set up benefits services<br>Set up workers comp vendor<br>Create job descriptions for current</p>
    <svg class="go" width="18" height="18" viewBox="0 0 18 18"><circle cx="9" cy="9" r="9" fill="#f5c10e"/><path d="M5 9h7M9 5.5L12.5 9 9 12.5" stroke="#5a5a5c" stroke-width="2" fill="none"/></svg>
  </article>

  <article class="abs service" style="left:300px">
    <svg width="60" height="60" viewBox="0 0 60 60" fill="none" stroke="#f5c10e" stroke-width="2"><circle cx="30" cy="12" r="8"/><circle cx="10" cy="28" r="6"/><circle cx="50" cy="28" r="6"/><path d="M18 56V36h24v20M30 20v16"/></svg>
    <h3>Managing HR Functions/Recruiting</h3>
    <p>Onboarding/Offboarding<br>Employee relations<br>Investigations<br>Leave administration<br>Immigration liaison<br>Compensation management</p>
    <svg class="go" width="18" height="18" viewBox="0 0 18 18"><circle cx="9" cy="9" r="9" fill="#f5c10e"/><path d="M5 9h7M9 5.5L12.5 9 9 12.5" stroke="#5a5a5c" stroke-width="2" fill="none"/></svg>
  </article>

  <article class="abs service featured" style="left:600px" role="img" aria-label="Photo of people reviewing documents at a desk behind the card">
    <svg width="60" height="60" viewBox="0 0 60 60" fill="none" stroke="#f5c10e" stroke-width="2"><rect x="4" y="30" width="22" height="26"/><rect x="34" y="4" width="22" height="26"/><circle cx="45" cy="14" r="5"/><circle cx="15" cy="40" r="5"/><path d="M26 43h12V30"/></svg>
    <h3>Recurring Procedures</h3>
    <p>Review handbook annually<br>Roll out training (required and soft skills training)<br>Write offer letters<br>Handle employee data and files<br>Conduct I-9 audits<br>Handle merit and review bonuses</p>
    <svg class="go" width="18" height="18" viewBox="0 0 18 18"><circle cx="9" cy="9" r="9" fill="#f5c10e"/><path d="M5 9h7M9 5.5L12.5 9 9 12.5" stroke="#3f4450" stroke-width="2" fill="none"/></svg>
  </article>

  <article class="abs service" style="left:900px">
    <svg width="60" height="60" viewBox="0 0 60 60" fill="none" stroke="#f5c10e" stroke-width="2"><circle cx="14" cy="12" r="7"/><circle cx="32" cy="12" r="7"/><path d="M4 56V28h38v28M44 56V44M50 56V38M56 56V32"/></svg>
    <h3>Partner Communications &amp; Projects</h3>
    <p>Manage annual bidding process for benefits review<br>Handle workers compensation claims administration<br>Manage leave administration</p>
    <svg class="go" width="18" height="18" viewBox="0 0 18 18"><circle cx="9" cy="9" r="9" fill="#f5c10e"/><path d="M5 9h7M9 5.5L12.5 9 9 12.5" stroke="#5a5a5c" stroke-width="2" fill="none"/></svg>
  </article>
</section>

<section>
  <h2 class="abs section how-title">HOW IT WORKS</h2>

  <article class="abs step" style="left:111px;top:2009px">
    <svg width="60" height="56" viewBox="0 0 60 56" fill="none" stroke="#f5c10e" stroke-width="2"><rect x="24" y="4" width="32" height="40"/><circle cx="14" cy="22" r="8"/><path d="M2 54V40h24v14M30 14h20M30 22h20M30 30h14"/></svg>
    <div class="label">STEP : 1</div><h3>Nemo enim ipsam</h3>
    <p>Lorem ipsum dolor sit amet, consect etur adipiscing elit, sed do eiusmod tempor incididunt ut labore et dolore magna aliqua Lorem ipsum dolor sit amet, consectetur adipiscing elit, sed do eiusmod tempor incididunt ut labore et dolore magna aliqua.</p>
  </article>
  <article class="abs step hot" style="left:443px;top:2009px">
    <svg width="60" height="56" viewBox="0 0 60 56" fill="none" stroke="#ffffff" stroke-width="2"><rect x="4" y="4" width="52" height="46"/><path d="M4 14h52"/><circle cx="26" cy="32" r="10"/><path d="M33 39l10 10"/></svg>
    <div class="label">STEP : 2</div><h3>Nemo enim ipsam</h3>
    <p>Lorem ipsum dolor sit amet, consect etur adipiscing elit, sed do eiusmod tempor incididunt ut labore et dolore magna aliqua Lorem ipsum dolor sit amet, consectetur adipiscing elit, sed do eiusmod tempor incididunt ut labore et dolore magna aliqua.</p>
  </article>
  <article class="abs step" style="left:776px;top:2009px">
    <svg width="60" height="56" viewBox="0 0 60 56" fill="none" stroke="#f5c10e" stroke-width="2"><circle cx="30" cy="28" r="26"/><ellipse cx="30" cy="28" rx="12" ry="26"/><path d="M4 28h52M8 16h44M8 40h44"/></svg>
    <div class="label">STEP : 3</div><h3>Nemo enim ipsam</h3>
    <p>Lorem ipsum dolor sit amet, consect etur adipiscing elit, sed do eiusmod tempor incididunt ut labore et dolore magna aliqua Lorem ipsum dolor sit amet, consectetur adipiscing elit, sed do eiusmod tempor incididunt ut labore et dolore magna aliqua.</p>
  </article>
  <article class="abs step" style="left:111px;top:2387px">
    <svg width="60" height="56" viewBox="0 0 60 56" fill="none" stroke="#f5c10e" stroke-width="2"><path d="M4 20h12l24-14v44L16 36H4zM12 36l4 16h6l-4-16M46 18l8-4M46 28h10M46 38l8 4"/></svg>
    <div class="label">STEP : 4</div><h3>Nemo enim ipsam</h3>
    <p>Lorem ipsum dolor sit amet, consect etur adipiscing elit, sed do eiusmod tempor incididunt ut labore et dolore magna aliqua Lorem ipsum dolor sit amet, consectetur adipiscing elit, sed do eiusmod tempor incididunt ut labore et dolore magna aliqua.</p>
  </article>
  <article class="abs step" style="left:443px;top:2387px">
    <svg width="60" height="56" viewBox="0 0 60 56" fill="none" stroke="#f5c10e" stroke-width="2"><circle cx="30" cy="10" r="6"/><circle cx="12" cy="24" r="5"/><circle cx="48" cy="24" r="5"/><path d="M4 54h52M20 54V30h20v24M4 42h16M40 42h16"/></svg>
    <div class="label">STEP : 5</div><h3>Nemo enim ipsam</h3>
    <p>Lorem ipsum dolor sit amet, consect etur adipiscing elit, sed do eiusmod tempor incididunt ut labore et dolore magna aliqua Lorem ipsum dolor sit amet, consectetur adipiscing elit, sed do eiusmod tempor incididunt ut labore et dolore magna aliqua.</p>
  </article>
  <article class="abs step" style="left:776px;top:2387px">
    <svg width="60" height="56" viewBox="0 0 60 56" fill="none" stroke="#f5c10e" stroke-width="2"><rect x="6" y="4" width="20" height="12"/><rect x="34" y="4" width="20" height="12"/><circle cx="16" cy="24" r="5"/><circle cx="44" cy="24" r="5"/><path d="M2 36h56M10 36v18M50 36v18M22 36v18M38 36v18"/></svg>
    <div class="label">STEP : 6</div><h3>Nemo enim ipsam</h3>
    <p>Lorem ipsum dolor sit amet, consect etur adipiscing elit, sed do eiusmod tempor incididunt ut labore et dolore magna aliqua Lorem ipsum dolor sit amet, consectetur adipiscing elit, sed do eiusmod tempor incididunt ut labore et dolore magna aliqua.</p>
  </article>
</section>

<section>
  <div class="abs team" role="img" aria-label="Photo of three colleagues in a relaxed office conversation"></div>
  <div class="abs team-rule"></div>
  <div class="abs team-rule bottom"></div>
  <h2 class="abs section team-title">OUR TEAM</h2>
  <p class="abs team-sub">Our team is woman-owned, women-led and partnership-oriented</p>
  <div class="abs play"><svg width="58" height="58" viewBox="0 0 58 58"><polygon points="23,18 40,29 23,40" fill="#222"/></svg></div>
</section>

<section>
  <h2 class="abs section say-title">WHAT THEY'RE SAYING</h2>
  <div class="abs quote"><svg width="68" height="68" viewBox="0 0 68 68"><text x="34" y="56" text-anchor="middle" font-family="Montserrat,sans-serif" font-size="56" font-weight="700" fill="#555">&#8220;</text></svg></div>
  <p class="abs say-text">"Lorem ipsum dolor sit amet, consectetur adipiscing elit, sed do eiusmod tempor incididunt ut labore et dolore magna aliqua. Ut enim ad minim veniam, quis nostrud exercitation ullamco laboris nisi ut aliquip ex ea commodo consequat. Duis aute irure dolor in reprehenderit in voluptate velit esse cillum dolore eu fugiat nulla pariatur. Excepteur sint occaecat cupidatat non proident, sunt in culpa qui officia deserunt mollit anim id est laborum."</p>
  <p class="abs say-name">- John Doe</p>
  <div class="abs dots"><span></span><span class="on"></span><span></span><span></span><span></span></div>

  <svg class="abs" style="left:48px;top:3884px" width="16" height="24" viewBox="0 0 16 24"><path d="M12 3L4 12l8 9" stroke="#222" stroke-width="2.5" fill="none"/></svg>
  <div class="abs client" style="left:111px"><i></i>Norvale</div>
  <div class="abs client" style="left:309px">Elmstead</div>
  <div class="abs client" style="left:507px">Brandora</div>
  <div class="abs client" style="left:705px">Ideaform</div>
  <div class="abs client" style="left:903px">Tallis Co</div>
  <svg class="abs" style="left:1134px;top:3884px" width="16" height="24" viewBox="0 0 16 24"><path d="M4 3l8 9-8 9" stroke="#222" stroke-width="2.5" fill="none"/></svg>
</section>

<footer>
  <div class="abs footer"></div>
  <div class="abs fcol" style="left:111px"><h4>QUICK LINKS</h4><ul><li>Home</li><li>About</li><li>Services</li><li>Team</li><li>Contact Us</li></ul></div>
  <div class="abs fcol" style="left:367px"><h4>FAQ</h4><ul><li>Sed ut perspiciatis unde</li><li>Amnis iste natus error sit</li><li>Voluptatem accusantium</li><li>Doloremque Sed ut perspiciatis</li><li>Unde omnis iste natus error</li></ul></div>
  <div class="abs fcol" style="left:660px"><h4>CONTACT US</h4><ul>
    <li class="ic"><svg width="10" height="13" viewBox="0 0 10 13"><path d="M5 0a5 5 0 0 1 5 5c0 3.5-5 8-5 8S0 8.5 0 5a5 5 0 0 1 5-5z" fill="#f5c10e"/><circle cx="5" cy="5" r="1.8" fill="#1b1b1b"/></svg><span>Sed ut perspiciatis unde<br>Amnis iste natus</span></li>
    <li class="ic" style="margin-top:8px"><svg width="11" height="11" viewBox="0 0 24 24"><path d="M6.6 10.8a15 15 0 0 0 6.6 6.6l2.2-2.2a1 1 0 0 1 1-.25 11.4 11.4 0 0 0 3.6.6 1 1 0 0 1 1 1V20a1 1 0 0 1-1 1A17 17 0 0 1 3 4a1 1 0 0 1 1-1h3.5a1 1 0 0 1 1 1c0 1.25.2 2.45.6 3.6a1 1 0 0 1-.25 1z" fill="#f5c10e"/></svg><span>+1 888 888 8888</span></li>
    <li class="ic"><svg width="12" height="10" viewBox="0 0 12 10"><rect width="12" height="10" fill="#f5c10e"/><path d="M0 0l6 5 6-5" stroke="#1b1b1b" fill="none"/></svg><span>info@companyname.com</span></li>
  </ul></div>
  <div class="abs fcol" style="left:941px"><h4>SOCIAL MEDIA</h4><ul><li>Friendloop</li><li>Chirpline</li><li>Snapgrid</li><li>Clipstream</li><li>Worklink</li></ul></div>
  <div class="abs frule"></div>
  <p class="abs copy">© Copyrights 2021 Company name | All Rights reserved</p>
</footer>

</body>
</html>
```